Coastline Premier Retreats Business Card Design

Design a business card for Coastline Premier Retreats. Look at the website for colors and reference. Card should have logo, name, title, office number, mobile number, email, URL and a tagline like, "Luxury Hotel & Resort Email Marketing" (This might change).

https://www.coastlinepremierretreats.example

The rest I will leave up to your imagination.

Contact Information for Business Card

Logo, name, title, office number, mobile number, email, URL and a tagline like, "Luxury Hotel & Resort Email Marketing" (This might change).

```html
<!DOCTYPE html>
<html lang="en">
<head>
<meta charset="utf-8">
<title>Coastline Premier Retreats – Business Card</title>
<link href="https://fonts.googleapis.com/css2?family=Arimo:wght@400;700&display=swap" rel="stylesheet">
<style>
  :root {
    --backdrop: #0f0f0f;
    --card: #1c1c1c;
    --accent: #e8741a;
    --ink: #f2f2f2;
  }
  * { margin: 0; padding: 0; box-sizing: border-box; }
  html, body { width: 1200px; height: 1059px; overflow: hidden; }
  body {
    background: var(--backdrop);
    font-family: "Arimo", Arial, sans-serif;
    color: var(--ink);
    position: relative;
  }
  .card {
    position: absolute;
    background: var(--card);
    box-shadow: 0 14px 30px rgba(0,0,0,.6);
  }
  .card-front { left: 257px; top: 89px; width: 687px; height: 390px; }
  .card-back  { left: 254px; top: 546px; width: 694px; height: 395px; }

  .frame {
    position: absolute;
    left: 22px; top: 22px; width: 643px; height: 337px;
    border: 2px solid var(--accent);
    border-bottom: none;
  }
  .frame-base {
    position: absolute; top: 357px; height: 2px; background: var(--accent);
  }
  .frame-base.left  { left: 22px;  width: 156px; }
  .frame-base.right { left: 510px; width: 155px; }
  .tagline {
    position: absolute; left: 178px; width: 332px; top: 347px;
    text-align: center; font-size: 17px; letter-spacing: .1px;
  }

  .wordmark {
    position: absolute; left: 0; right: 0;
    text-align: center; font-weight: 700; text-transform: uppercase;
    color: var(--ink); white-space: nowrap;
  }
  .card-front .wordmark { top: 88px; font-size: 21px; letter-spacing: 1.5px; }
  .card-back  .wordmark { top: 178px; font-size: 36px; letter-spacing: 2px; }

  .identity {
    position: absolute; right: 361px; top: 200px; text-align: right;
  }
  .identity .person {
    color: var(--accent); font-weight: 700; font-size: 29px; line-height: 32px;
  }
  .identity .role { font-size: 16px; margin-top: 1px; letter-spacing: .4px; }
  .identity .address { font-size: 16px; line-height: 20px; margin-top: 10px; }

  .divider {
    position: absolute; left: 348px; top: 203px; width: 1px; height: 89px;
    background: var(--accent);
  }

  .contacts {
    position: absolute; left: 376px; top: 200px; list-style: none;
    font-size: 14.5px;
  }
  .contacts li { display: flex; align-items: center; height: 25px; }
  .contacts svg { width: 12px; height: 12px; margin-right: 9px; flex: none; }
</style>
</head>
<body>

<section class="card card-front">
  <div class="frame"></div>
  <div class="frame-base left"></div>
  <div class="frame-base right"></div>
  <p class="tagline">Luxury Hotel &amp; Resort Email Marketing</p>

  <div class="wordmark">Coastline Premier Retreats</div>

  <div class="identity">
    <div class="person">DANIEL REYES</div>
    <div class="role">CEO/Founder</div>
    <div class="address">Po Box, 48 B Harbor Rd<br>Seaside Bay, CA 93021</div>
  </div>

  <div class="divider"></div>

  <ul class="contacts">
    <li>
      <svg viewBox="0 0 12 12"><rect x="3" y="0.5" width="6" height="11" rx="1" fill="none" stroke="#e8741a" stroke-width="1.2"/><circle cx="6" cy="9.6" r=".7" fill="#e8741a"/></svg>
      555.204.7100
    </li>
    <li>
      <svg viewBox="0 0 12 12"><path d="M1 5 Q6 1 11 5 L10 6.5 L8 5.5 L8 4.5 Q6 3.8 4 4.5 L4 5.5 L2 6.5 Z" fill="#e8741a"/><rect x="2.5" y="7" width="7" height="4" rx=".6" fill="#e8741a"/></svg>
      +34 600 412 873
    </li>
    <li>
      <svg viewBox="0 0 12 12"><path d="M1 4.5 L6 1 L11 4.5 V11 H1 Z" fill="#e8741a"/><path d="M1 4.5 L6 8 L11 4.5" fill="none" stroke="#1c1c1c" stroke-width="1"/></svg>
      info@coastlinepremierretreats.example
    </li>
    <li>
      <svg viewBox="0 0 12 12"><circle cx="6" cy="6" r="5.3" fill="#e8741a"/><path d="M3 3.5 Q5 4 4.5 6 Q6 7 5 9.5 M7.5 2 Q8 4 9.5 4.5 M8 7.5 Q9 8 8.5 10" fill="none" stroke="#1c1c1c" stroke-width="1"/></svg>
      www.coastlinepremierretreats.example
    </li>
  </ul>
</section>

<section class="card card-back">
  <div class="wordmark">Coastline Premier Retreats</div>
</section>

</body>
</html>
```